Looking for someone to design a business card for my plumbing business Quandor Plumbing Solutions I want the background also to be black, must attract clients. If possible I want the front to be the logo and the back to show maybe the details.

Target Market(s)

Clients

Industry/Entity Type

Plumbing maintenance

Contact Information for Business Card

Name: Felix, Contact: 0461 539 207, Email: quandorplumbingsolutions@mailbrook.example, Licence number 728093K

Font styles to use
Other font styles liked:
• as per logo maybe?

Colors

Designer to choose colors to be used in the design.

Requirements
Nice to have
• stating the service I provide, emergency plumbing, plumbing maintenance, drainage maintenance, block sewer and stormwater, camera and locating.

```html
<!DOCTYPE html>
<html lang="en">
<head>
<meta charset="utf-8">
<title>Quandor Plumbing Solutions – Business Card</title>
<link href="https://fonts.googleapis.com/css2?family=Montserrat:wght@400;500;700;800&display=swap" rel="stylesheet">
<style>
  :root {
    --backdrop: #141414;
    --card: #1f1f1f;
    --ink: #f2f2f2;
    --accent: #4a8fd4;
    --shadow: rgba(0,0,0,0.6);
  }
  * { box-sizing: border-box; margin: 0; padding: 0; }
  html, body {
    width: 1200px; height: 1059px; overflow: hidden;
    background: var(--backdrop);
    font-family: "Montserrat", sans-serif;
    color: var(--ink);
  }
  .canvas { position: relative; width: 1200px; height: 1059px; }
  .card {
    position: absolute;
    background: var(--card);
    border-radius: 18px;
    box-shadow: 0 10px 24px var(--shadow);
  }
  .card--details { left: 257px; top: 89px; width: 687px; height: 390px; }
  .card--brand { left: 254px; top: 547px; width: 693px; height: 393px; }

  .holder { position: absolute; left: 45px; top: 56px; }
  .holder__name {
    font-weight: 800; font-size: 24px; letter-spacing: 0.5px;
    color: var(--accent); line-height: 1;
  }
  .holder__role { font-size: 15px; font-weight: 400; margin-top: 3px; }

  .contact { position: absolute; left: 45px; top: 155px; list-style: none; font-size: 15px; }
  .contact__licence { margin-bottom: 15px; }
  .contact__item { display: flex; align-items: center; height: 26px; }
  .contact__icon { width: 14px; height: 14px; margin-right: 6px; flex: none; }

  .services {
    position: absolute; left: 45px; top: 290px; width: 620px;
    list-style: none; font-size: 15px; display: flex; flex-wrap: wrap;
    row-gap: 10px; column-gap: 10px;
  }
  .services li { display: flex; align-items: center; }
  .services li::before {
    content: ""; width: 5px; height: 5px; border-radius: 50%;
    background: var(--accent); margin-right: 8px;
  }

  .wordmark {
    position: absolute; display: flex; align-items: center;
    color: var(--accent); font-weight: 800; text-transform: uppercase; line-height: 1.05;
  }
  .wordmark__dot { border-radius: 50%; background: var(--accent); flex: none; }
  .wordmark--small { left: 400px; top: 62px; font-size: 24px; }
  .wordmark--small .wordmark__dot { width: 54px; height: 54px; margin-right: 14px; }
  .wordmark--large { left: 0; right: 0; top: 0; bottom: 0; justify-content: center; font-size: 40px; }
  .wordmark--large .wordmark__dot { width: 96px; height: 96px; margin-right: 22px; }
</style>
</head>
<body>
<main class="canvas">
  <section class="card card--details">
    <div class="holder">
      <p class="holder__name">FELIX</p>
      <p class="holder__role">Founder &amp; CEO</p>
    </div>

    <div class="wordmark wordmark--small">
      <span class="wordmark__dot"></span>
      <span>Quandor<br>Plumbing<br>Solutions</span>
    </div>

    <ul class="contact">
      <li class="contact__licence">Licence number 728093K</li>
      <li class="contact__item">
        <svg class="contact__icon" viewBox="0 0 24 24"><path fill="#4a8fd4" d="M6.6 10.8a15.1 15.1 0 0 0 6.6 6.6l2.2-2.2c.3-.3.7-.4 1-.2 1.1.4 2.3.6 3.6.6.6 0 1 .4 1 1V20c0 .6-.4 1-1 1A17 17 0 0 1 3 4c0-.6.4-1 1-1h3.5c.6 0 1 .4 1 1 0 1.3.2 2.5.6 3.6.1.3 0 .7-.2 1z"/></svg>
        0461 539 207
      </li>
      <li class="contact__item">
        <svg class="contact__icon" viewBox="0 0 24 24"><rect x="2" y="5" width="20" height="14" fill="#4a8fd4"/><path d="M2 5l10 8 10-8" fill="none" stroke="#1f1f1f" stroke-width="2"/></svg>
        quandorplumbingsolutions@mailbrook.example
      </li>
      <li class="contact__item">
        <svg class="contact__icon" viewBox="0 0 24 24"><circle cx="12" cy="12" r="11" fill="#4a8fd4"/></svg>
        @QuandorPlumbingSolutions
      </li>
    </ul>

    <ul class="services">
      <li>Emergency plumbing</li>
      <li>Plumbing maintenance</li>
      <li>Drainage maintenance</li>
      <li>Block sewer and stormwater</li>
      <li>Camera and locating</li>
    </ul>
  </section>

  <section class="card card--brand">
    <div class="wordmark wordmark--large">
      <span class="wordmark__dot"></span>
      <span>Quandor<br>Plumbing Solutions</span>
    </div>
  </section>
</main>
</body>
</html>
```